Business Card Design

Printing and photocopying solutions, computer sales, photocopier sales and service, stationery needs

We aim to be the best for reliability, knowledge, skilled technical ability and highly ethical in business dealings. We would like to present as professional and the key person for dealing with for all customers. We are based in the Solomon Islands and therefore part of a developing country where many services and infrastructures are not in place. We would like to be seen as leading the field with technology and advanced office support. We strongly support the community and education systems with our current services and are seeking to expand the reach to encompass other service offerings

Target Market(s)

Business, Schools, Government offices, Churches, Non-government organisations

Industry/Entity Type

Business

Contact Information for Business Card

Harbourlight Print
harbourlightprint@mailvane.example
+677 7418062 +677 8205147
PO Box 8
Auki, Malaita Province
Solomon Islands

Requirements
Must have
• professional appearance. Some Blue colouring
Must have easy to read phone number so required the phone number to be large font

Must have Shop address as well
Shop 7, Tidewell Building
Auki, Malaita, Solomon Islands
Nice to have
• Keep simple and professional with appearance of the business card styles, use the back of the card for Logo and a list of the basic services that is offered from Harbourlight Print

```html
<!DOCTYPE html>
<html lang="en">
<head>
<meta charset="utf-8">
<title>Harbourlight Print — Business Card</title>
<link href="https://fonts.googleapis.com/css2?family=Exo+2:wght@400;500;600&display=swap" rel="stylesheet">
<style>
  :root {
    --backdrop: #c9c9cb;
    --paper: #f7f8f9;
    --ink: #3a3a3c;
    --brand-blue: #1b7fd0;
    --brand-deep: #1d4fa8;
    --bar-dark: #2a2a2c;
    --bar-light: #d6d6d8;
  }
  * { box-sizing: border-box; margin: 0; padding: 0; }
  html, body { width: 1200px; height: 894px; overflow: hidden; }
  body {
    background: var(--backdrop);
    font-family: "Exo 2", sans-serif;
    color: var(--ink);
    position: relative;
  }
  .card {
    position: absolute;
    width: 520px;
    height: 298px;
    border-radius: 3px;
    box-shadow: 0 10px 24px rgba(0,0,0,.22);
    overflow: hidden;
  }
  .card--front { left: 50px; top: 298px; background: var(--paper); }
  .card--back {
    left: 630px; top: 298px;
    background: radial-gradient(ellipse at 60% 45%, #1a8fdc 0%, var(--brand-blue) 35%, var(--brand-deep) 100%);
  }

  .brand-name {
    font-weight: 500;
    letter-spacing: .5px;
    white-space: nowrap;
  }
  .card--front .brand-name {
    position: absolute; right: 30px; top: 36px;
    font-size: 30px; color: var(--brand-deep);
  }
  .card--back .brand-name {
    position: absolute; left: 0; right: 0; top: 124px;
    text-align: center; font-size: 40px; color: #ffffff;
  }

  .person { position: absolute; left: 36px; top: 100px; }
  .person__name { font-size: 17px; font-weight: 600; color: var(--brand-blue); letter-spacing: 1px; text-transform: uppercase; }
  .person__role { font-size: 11px; font-weight: 500; letter-spacing: 1px; text-transform: uppercase; margin-top: 1px; }

  .contact-line {
    position: absolute;
    display: flex; align-items: flex-start; gap: 8px;
    font-size: 12.5px; line-height: 17px;
    white-space: nowrap;
  }
  .contact-line svg { flex: none; margin-top: 3px; }
  .contact-line--address { left: 36px; top: 148px; }
  .contact-line--web { left: 36px; top: 188px; }

  .bar--dark {
    position: absolute; left: 0; top: 222px; width: 240px; height: 8px;
    background: linear-gradient(90deg, var(--bar-dark) 0%, #6a6a6c 55%, var(--bar-light) 100%);
  }
  .bar--blue {
    position: absolute; right: 0; bottom: 20px; width: 250px; height: 8px;
    background: linear-gradient(90deg, var(--brand-blue) 0%, var(--brand-deep) 100%);
  }

  .phones { position: absolute; left: 272px; top: 176px; }
  .phones .contact-line { position: static; margin-bottom: 3px; }
  .phones .contact-line--phone { font-size: 18px; line-height: 22px; font-weight: 600; letter-spacing: .5px; }
  .phones .contact-line--phone svg { margin-top: 5px; }
  .phones .contact-line--email { font-size: 11.5px; margin-top: 2px; }
</style>
</head>
<body>

<section class="card card--front" aria-label="Business card front">
  <div class="brand-name">Harbourlight Print</div>

  <div class="person">
    <div class="person__name">Daniel Kerrow</div>
    <div class="person__role">General Manager</div>
  </div>

  <div class="contact-line contact-line--address">
    <svg width="10" height="13" viewBox="0 0 10 13" aria-hidden="true"><path d="M5 0a5 5 0 0 1 5 5c0 3.5-5 8-5 8S0 8.5 0 5a5 5 0 0 1 5-5z" fill="var(--brand-blue)"/><circle cx="5" cy="5" r="1.8" fill="#fff"/></svg>
    <span>Shop 7, Tidewell Building<br>Auki, Malaita</span>
  </div>

  <div class="contact-line contact-line--web">
    <svg width="11" height="11" viewBox="0 0 12 12" aria-hidden="true"><circle cx="6" cy="6" r="5.3" fill="none" stroke="var(--brand-blue)" stroke-width="1.2"/><ellipse cx="6" cy="6" rx="2.3" ry="5.3" fill="none" stroke="var(--brand-blue)" stroke-width="1"/><line x1="0.7" y1="6" x2="11.3" y2="6" stroke="var(--brand-blue)" stroke-width="1"/></svg>
    <span>www.harbourlightprint.example</span>
  </div>

  <div class="bar--dark"></div>

  <div class="phones">
    <div class="contact-line contact-line--phone">
      <svg width="13" height="13" viewBox="0 0 12 12" aria-hidden="true"><path d="M2.5 0.8l2 2.2-1 1.4a7 7 0 0 0 4 4l1.4-1 2.2 2-1.2 1.8C5.5 11 1 6.5 0.8 2z" fill="var(--brand-blue)"/></svg>
      <span>+677 7418062</span>
    </div>
    <div class="contact-line contact-line--phone">
      <svg width="13" height="14" viewBox="0 0 9 13" aria-hidden="true"><rect x="0.6" y="0.6" width="7.8" height="11.8" rx="1.4" fill="none" stroke="var(--brand-blue)" stroke-width="1.2"/><rect x="3" y="10" width="3" height="1" fill="var(--brand-blue)"/></svg>
      <span>+677 8205147</span>
    </div>
    <div class="contact-line contact-line--email">
      <svg width="12" height="9" viewBox="0 0 12 9" aria-hidden="true"><rect width="12" height="9" rx="1" fill="var(--brand-blue)"/><path d="M0.5 0.8L6 5l5.5-4.2" fill="none" stroke="#fff" stroke-width="1"/></svg>
      <span>harbourlightprint@mailvane.example</span>
    </div>
  </div>

  <div class="bar--blue"></div>
</section>

<section class="card card--back" aria-label="Business card back">
  <div class="brand-name">Harbourlight Print</div>
</section>

</body>
</html>
```